Torvane Halbridge

Looking for modern business cards.
Clean contemporary design.
Similar to this.
https://www.plumvexa-search.example/imgres?imgurl=https%3A%2F%2Fimg.quorlint-cdn.example%2Fsleek_dark_metal_card_design_540.jpg&imgrefurl=https%3A%2F%2Fwww.quorlint-prints.example%2Fsleek_dark_metal_card_design-918273645501928374&q=modern%20business%20cards

But I'd like the blue to look metallic.

Business

```html
<!DOCTYPE html>
<html lang="en">
<head>
<meta charset="utf-8">
<title>Torvane Halbridge — Business Card</title>
<link rel="stylesheet" href="https://fonts.googleapis.com/css2?family=Open+Sans:wght@400;600&display=swap">
<style>
  :root {
    --canvas: #ecedef;
    --paper: #ffffff;
    --navy: #22566f;
    --navy-light: #2f6f8d;
    --navy-deep: #1a4458;
    --cyan: #18a3c6;
    --cyan-light: #5cc6e0;
    --brand-ink: #1f5a74;
    --accent-red: #e8341c;
    --text-light: #ffffff;
  }
  * { margin: 0; padding: 0; box-sizing: border-box; }
  html, body { width: 1200px; height: 900px; overflow: hidden; }
  body {
    position: relative;
    background: var(--canvas);
    font-family: "Open Sans", Arial, sans-serif;
  }
  .card {
    position: absolute;
    overflow: hidden;
    box-shadow: 0 6px 18px rgba(0,0,0,0.18);
  }
  .card svg.card-bg { position: absolute; inset: 0; display: block; }
  .card-front { left: 178px; top: 75px; width: 588px; height: 363px; background: var(--paper); }
  .card-back  { left: 388px; top: 505px; width: 567px; height: 352px; background: var(--navy); }

  .brand {
    position: absolute;
    display: flex;
    align-items: center;
    gap: 14px;
    font-weight: 600;
    letter-spacing: -0.5px;
    white-space: nowrap;
  }
  .brand-dot { border-radius: 50%; flex: none; }
  .card-front .brand { left: 116px; top: 92px; font-size: 38px; color: var(--brand-ink); }
  .card-front .brand-dot { width: 15px; height: 15px; background: var(--accent-red); }
  .card-back .brand { left: 46px; top: 250px; font-size: 34px; color: var(--text-light); }
  .card-back .brand-dot { width: 14px; height: 14px; background: var(--text-light); }

  .holder {
    position: absolute; right: 326px; top: 256px;
    text-align: right; color: var(--text-light);
  }
  .holder-name { font-size: 19px; font-weight: 600; line-height: 1.2; }
  .holder-title { font-size: 15px; line-height: 1.3; }

  .contact-list {
    position: absolute; left: 292px; top: 245px;
    list-style: none; color: var(--text-light); font-size: 15px; line-height: 21.5px;
  }
  .contact-list li { display: flex; align-items: center; gap: 6px; white-space: nowrap; }
  .contact-icon { width: 11px; height: 11px; flex: none; display: block; }

  .address {
    position: absolute; left: 90px; top: 317px;
    color: var(--text-light); font-size: 15px; white-space: nowrap;
  }
</style>
</head>
<body>

<section class="card card-front" aria-label="Business card front">
  <svg class="card-bg" width="588" height="363" viewBox="0 0 588 363" aria-hidden="true">
    <defs>
      <linearGradient id="navyMetal" x1="0" y1="0" x2="1" y2="1">
        <stop offset="0" stop-color="#1d4b61"/>
        <stop offset="0.45" stop-color="#3a7a97"/>
        <stop offset="0.55" stop-color="#2a6580"/>
        <stop offset="1" stop-color="#1a4458"/>
      </linearGradient>
      <linearGradient id="cyanMetal" x1="0" y1="0" x2="1" y2="0">
        <stop offset="0" stop-color="#1497b9"/>
        <stop offset="0.5" stop-color="#6fd0e8"/>
        <stop offset="1" stop-color="#1a9fc2"/>
      </linearGradient>
    </defs>
    <polygon points="0,220 384,220 412,183 588,183 588,363 0,363" fill="url(#navyMetal)"/>
    <polygon points="0,192 405,192 386,217 0,217" fill="url(#cyanMetal)"/>
  </svg>

  <div class="brand"><span>Torvane Halbridge</span><span class="brand-dot"></span></div>

  <div class="holder">
    <p class="holder-name">ELRIC VANTOE</p>
    <p class="holder-title">Managing Director</p>
  </div>

  <ul class="contact-list">
    <li>
      <svg class="contact-icon" viewBox="0 0 12 12" aria-hidden="true"><path d="M2.5 1 L4.5 1 L5.3 3.5 L4 4.5 Q5 7 7.5 8 L8.5 6.7 L11 7.5 L11 9.5 Q10.5 11 9 11 Q1 10 1 2.5 Q1 1 2.5 1 Z" fill="#fff"/></svg>
      055-214 387 610
    </li>
    <li>
      <svg class="contact-icon" viewBox="0 0 12 12" aria-hidden="true"><rect x="1" y="2.5" width="10" height="7" fill="#fff"/><path d="M1 2.5 L6 6.5 L11 2.5" fill="none" stroke="#22566f" stroke-width="1"/></svg>
      hello@torvanehalbridge.example
    </li>
    <li>
      <svg class="contact-icon" viewBox="0 0 12 12" aria-hidden="true"><circle cx="6" cy="6" r="5" fill="none" stroke="#fff" stroke-width="1.2"/><ellipse cx="6" cy="6" rx="2.2" ry="5" fill="none" stroke="#fff" stroke-width="1"/><line x1="1" y1="6" x2="11" y2="6" stroke="#fff" stroke-width="1"/></svg>
      www.torvanehalbridge.example
    </li>
  </ul>

  <p class="address">12345, Address Goes Here, Country Name here, 123456.</p>
</section>

<section class="card card-back" aria-label="Business card back">
  <svg class="card-bg" width="567" height="352" viewBox="0 0 567 352" aria-hidden="true">
    <defs>
      <linearGradient id="backNavy" x1="0" y1="0" x2="1" y2="1">
        <stop offset="0" stop-color="#1e4d63"/>
        <stop offset="0.48" stop-color="#336f8b"/>
        <stop offset="0.56" stop-color="#28637e"/>
        <stop offset="1" stop-color="#1b4559"/>
      </linearGradient>
      <linearGradient id="backCyan" x1="0" y1="0" x2="1" y2="1">
        <stop offset="0" stop-color="#1595b6"/>
        <stop offset="0.45" stop-color="#63cbe4"/>
        <stop offset="0.6" stop-color="#22a6c8"/>
        <stop offset="1" stop-color="#1490b0"/>
      </linearGradient>
    </defs>
    <rect width="567" height="352" fill="url(#backNavy)"/>
    <rect x="447" y="0" width="120" height="352" fill="url(#backCyan)"/>
  </svg>

  <div class="brand"><span>Torvane Halbridge</span><span class="brand-dot"></span></div>
</section>

</body>
</html>
```